Business card design Needed for new logo / Construction business, home extensions and new builds

We need a business card design using our new logo files which i will attach to this project :)

We are a small construction business specialising in home extensions, new builds and property development. We are very ambitious and would appreciate professional and elegant designs for our new business card.

Very serious about using the services on MakerQuarry and recently acquired our new logo from here :)

Please get involved, i will feedback when i can as i am very busy but can respond daily, thanks

Target Market(s)

People that want to build onto their houses, new building developments or adding too their existing property

Industry/Entity Type

Construction

Contact Information for Business Card

Renwick Tolliver Construction, Lionel Ashby (Managing Director), Tel 07822254961, email - info@renwick-tolliver, www.renwick-tolliver.co.uk

Colors

Designer to choose colors to be used in the design.

Requirements
Must have
• I like a deep grey on the back please. A lot of you have provided black from and back, try mixing things up a little. The black looks cool 😎 Thanks

```html
<!DOCTYPE html>
<html lang="en">
<head>
<meta charset="utf-8">
<title>Renwick Tolliver Construction – Business Card</title>
<link href="https://fonts.googleapis.com/css2?family=Open+Sans:wght@400;600;700&display=swap" rel="stylesheet">
<style>
  :root {
    --backdrop: #232323;
    --card: #1f2023;
    --card-deep: #191a1d;
    --layer: #222327;
    --gold: #e0a82e;
    --gold-light: #f2c660;
    --silver: #c9cbcf;
    --white: #f4f4f4;
  }
  * { margin: 0; padding: 0; box-sizing: border-box; }
  html, body { width: 1200px; height: 780px; overflow: hidden; }
  body {
    background: var(--backdrop);
    font-family: "Open Sans", Arial, sans-serif;
    position: relative;
  }
  .card {
    position: absolute;
    top: 70px;
    width: 400px;
    height: 640px;
    border-radius: 28px;
    background: var(--card);
    overflow: hidden;
    box-shadow: 0 18px 40px rgba(0,0,0,.55);
  }
  .card--front { left: 160px; }
  .card--back { left: 640px; }

  /* Front */
  .front-brand {
    position: absolute;
    left: 50%; top: 50%;
    transform: translate(-50%, -50%) rotate(-90deg);
    display: flex; align-items: center; gap: 22px;
    white-space: nowrap;
  }
  .brand-mark {
    width: 22px; height: 22px;
    background: var(--gold);
    flex: none;
  }
  .brand-name {
    color: var(--gold);
    font-weight: 600;
    text-transform: uppercase;
    letter-spacing: 3px;
    line-height: 1.35;
    text-align: center;
  }
  .front-brand .brand-name { font-size: 28px; }

  /* Back */
  .back-layers { position: absolute; inset: 0; }
  .back-brand {
    position: absolute; top: 70px; left: 0; right: 0;
    display: flex; flex-direction: column; align-items: center; gap: 16px;
  }
  .back-brand .brand-mark { width: 18px; height: 18px; }
  .back-brand .brand-name { font-size: 19px; }

  .holder {
    position: absolute; top: 228px; left: 0; right: 0;
    text-align: center;
  }
  .holder-name {
    font-size: 32px; font-weight: 700; letter-spacing: .5px;
  }
  .holder-name .first { color: var(--silver); }
  .holder-name .last { color: var(--gold); }
  .holder-role {
    color: var(--white); font-size: 15px; font-weight: 600; margin-top: 2px;
  }
  .contact-icons {
    display: flex; justify-content: center; gap: 10px; margin-top: 18px;
  }
  .icon-dot {
    width: 26px; height: 26px; border-radius: 50%;
    background: radial-gradient(circle at 35% 30%, var(--gold-light), var(--gold));
    display: flex; align-items: center; justify-content: center;
  }
  .contact-lines {
    list-style: none; margin-top: 18px;
    color: var(--white); font-size: 15px; line-height: 1.45;
  }
  .address {
    position: absolute; bottom: 58px; left: 0; right: 0;
    text-align: center; color: var(--white); font-size: 15px; line-height: 1.45;
  }
  .address .icon-dot { margin: 0 auto 12px; }
</style>
</head>
<body>

  <section class="card card--front" aria-label="Card front">
    <div class="front-brand">
      <span class="brand-mark"></span>
      <p class="brand-name">Renwick Tolliver<br>Construction</p>
    </div>
  </section>

  <section class="card card--back" aria-label="Card back">
    <svg class="back-layers" width="400" height="640" viewBox="0 0 400 640" aria-hidden="true">
      <defs>
        <linearGradient id="layerShade" x1="0" y1="0" x2="0" y2="1">
          <stop offset="0" stop-color="#17181b"/>
          <stop offset="1" stop-color="#202125"/>
        </linearGradient>
      </defs>
      <rect width="400" height="640" fill="#1e1f22"/>
      <path d="M0 470 C90 470 230 450 400 370 L400 640 L0 640 Z" fill="url(#layerShade)"/>
      <path d="M0 560 C120 520 220 470 300 440 C340 425 370 418 400 416 L400 640 L0 640 Z" fill="#1c1d20"/>
      <path d="M0 0 H400 V340 C330 430 230 462 0 462 Z" fill="#212226" filter="drop-shadow(0 6px 8px rgba(0,0,0,.5))"/>
    </svg>

    <header class="back-brand">
      <span class="brand-mark"></span>
      <p class="brand-name">Renwick Tolliver<br>Construction</p>
    </header>

    <div class="holder">
      <h1 class="holder-name"><span class="first">Lionel</span> <span class="last">Ashby</span></h1>
      <p class="holder-role">Managing Director</p>
      <div class="contact-icons">
        <span class="icon-dot" aria-label="Phone">
          <svg width="14" height="14" viewBox="0 0 24 24"><path d="M6.6 10.8a15 15 0 0 0 6.6 6.6l2.2-2.2c.3-.3.7-.4 1-.2 1.1.4 2.3.6 3.6.6.6 0 1 .4 1 1V20c0 .6-.4 1-1 1A17 17 0 0 1 3 4c0-.6.4-1 1-1h3.5c.6 0 1 .4 1 1 0 1.3.2 2.5.6 3.6.1.3 0 .7-.2 1z" fill="#1e1f22"/></svg>
        </span>
        <span class="icon-dot" aria-label="Email">
          <svg width="14" height="14" viewBox="0 0 24 24"><rect x="2" y="5" width="20" height="14" rx="2" fill="#1e1f22"/><path d="M3 6l9 7 9-7" stroke="#e0a82e" stroke-width="2" fill="none"/></svg>
        </span>
        <span class="icon-dot" aria-label="Website">
          <svg width="14" height="14" viewBox="0 0 24 24"><circle cx="12" cy="12" r="9" fill="none" stroke="#1e1f22" stroke-width="2.2"/><ellipse cx="12" cy="12" rx="4" ry="9" fill="none" stroke="#1e1f22" stroke-width="2"/><path d="M3 12h18" stroke="#1e1f22" stroke-width="2"/></svg>
        </span>
      </div>
      <ul class="contact-lines">
        <li>0782 225 4961</li>
        <li>info@renwick-tolliver.co.uk</li>
        <li>www.renwick-tolliver.co.uk</li>
      </ul>
    </div>

    <address class="address" style="font-style:normal">
      <span class="icon-dot" aria-label="Location">
        <svg width="14" height="14" viewBox="0 0 24 24"><path d="M12 2a7 7 0 0 0-7 7c0 5 7 13 7 13s7-8 7-13a7 7 0 0 0-7-7z" fill="#1e1f22"/><circle cx="12" cy="9" r="2.6" fill="#e0a82e"/></svg>
      </span>
      Alder Lane, Kestrel Vale<br>
      Westbury, WB4 7QN
    </address>
  </section>

</body>
</html>
```